Birchline Septic Solutions

Would like to see some single sided ones but would also like to see some double sided with one sided only being the logo. Owners name is Colin Vandro. Phone number is 555-214-0387
Services are pumping, inspections, installs, and repairs

Contact Information for Business Card

555-241-0387 Colin Vandro Larkton, OH

```html
<!DOCTYPE html>
<html lang="en">
<head>
<meta charset="utf-8">
<title>Birchline Septic Solutions – Business Card</title>
<link rel="stylesheet" href="https://fonts.googleapis.com/css2?family=Montserrat:wght@500;600;800&display=swap">
<style>
  :root {
    --backdrop: #2b2f36;
    --card: #ffffff;
    --ink: #1f1f1f;
    --teal: #2fbdb8;
    --muted: #d9d9d9;
  }
  html, body {
    margin: 0;
    padding: 0;
    width: 1200px;
    height: 900px;
    overflow: hidden;
    background: var(--backdrop);
    font-family: "Montserrat", sans-serif;
  }
  .canvas {
    position: relative;
    width: 1200px;
    height: 900px;
  }
  .card {
    position: absolute;
    left: 110px;
    top: 170px;
    width: 980px;
    height: 560px;
    background: var(--card);
    border-radius: 40px;
    overflow: hidden;
  }
  .brand {
    position: absolute;
    left: 380px;
    top: 90px;
    width: 520px;
    text-align: center;
    color: var(--ink);
    font-weight: 800;
    text-transform: uppercase;
  }
  .brand-name {
    display: block;
    font-size: 66px;
    letter-spacing: 2px;
    line-height: 1;
  }
  .brand-tagline {
    display: block;
    margin-top: 14px;
    font-size: 22px;
    letter-spacing: 9px;
    line-height: 1;
  }
  .owner-panel {
    position: absolute;
    left: 0;
    top: 300px;
    width: 352px;
    height: 205px;
    background: var(--ink);
    box-sizing: border-box;
    padding: 62px 0 0 36px;
  }
  .owner-name {
    margin: 0;
    color: var(--teal);
    font-size: 32px;
    font-weight: 600;
    text-transform: uppercase;
    letter-spacing: 0.5px;
    line-height: 1.1;
    white-space: nowrap;
  }
  .owner-location {
    margin: 10px 0 0;
    color: var(--muted);
    font-size: 22px;
    font-weight: 500;
    white-space: nowrap;
  }
  .phone-band {
    position: absolute;
    left: 372px;
    top: 320px;
    right: 0;
    height: 200px;
    background: var(--teal);
    display: flex;
    align-items: center;
    padding-left: 120px;
    gap: 26px;
    color: #ffffff;
  }
  .phone-icon {
    width: 40px;
    height: 40px;
    flex: none;
  }
  .phone-number {
    font-size: 58px;
    font-weight: 500;
    letter-spacing: 1px;
    white-space: nowrap;
  }
</style>
</head>
<body>
  <main class="canvas">
    <section class="card" aria-label="Business card front">
      <div class="brand">
        <span class="brand-name">Birchline</span>
        <span class="brand-tagline">Septic Solutions</span>
      </div>

      <div class="owner-panel">
        <h1 class="owner-name">Colin Vandro</h1>
        <p class="owner-location">Larkton, OH</p>
      </div>

      <div class="phone-band">
        <svg class="phone-icon" viewBox="0 0 24 24" aria-hidden="true">
          <path fill="#ffffff" d="M6.6 10.8a15.1 15.1 0 0 0 6.6 6.6l2.2-2.2a1 1 0 0 1 1-.25 11.4 11.4 0 0 0 3.6.57 1 1 0 0 1 1 1V20a1 1 0 0 1-1 1A17 17 0 0 1 3 4a1 1 0 0 1 1-1h3.5a1 1 0 0 1 1 1c0 1.25.2 2.45.57 3.57a1 1 0 0 1-.25 1z"/>
        </svg>
        <span class="phone-number">555-241-0387</span>
      </div>
    </section>
  </main>
</body>
</html>
```